Business Card For Halvenmoor Financial Consulting

Hi, I would like a business card designed. Bold, modern.
Please use the same design as the logo. I have also attached the website design to see the overall theme.
Wordmark Font
Color: Hex: #01AEF7

```html
<!DOCTYPE html>
<html lang="en">
<head>
<meta charset="utf-8">
<title>Halvenmoor Consulting – Business Card</title>
<link rel="stylesheet" href="https://fonts.googleapis.com/css2?family=Arimo:ital,wght@0,400;0,700;1,400&display=swap">
<style>
  :root {
    --page-bg: #0a0c0f;
    --card-bg: #121c24;
    --card-edge: #01aef7;
    --accent: #01aef7;
    --frame-tone: #1e2a33;
    --text-light: #f2f5f7;
  }
  * { margin: 0; padding: 0; box-sizing: border-box; }
  html, body {
    width: 1200px; height: 963px; overflow: hidden;
    background: var(--page-bg);
    font-family: "Arimo", Arial, sans-serif;
  }
  .sheet {
    width: 1200px; height: 963px;
    display: flex; flex-direction: column;
    align-items: center; justify-content: center; gap: 60px;
  }
  .card {
    position: relative;
    width: 600px; height: 343px;
    background: var(--card-bg);
    border-radius: 22px;
    border-right: 3px solid var(--card-edge);
    border-bottom: 3px solid var(--card-edge);
    overflow: hidden;
  }
  .backdrop-frame {
    position: absolute;
    border: 24px solid var(--frame-tone);
    z-index: 0;
  }
  .card-front .backdrop-frame { left: 300px; top: 190px; width: 260px; height: 260px; }
  .card-back .backdrop-frame { left: 150px; top: 40px; width: 380px; height: 380px; }
  .wordmark {
    display: flex; align-items: center; gap: 14px;
    position: absolute; z-index: 1;
    white-space: nowrap;
  }
  .wordmark-square {
    flex: none;
    width: 30px; height: 30px;
    border: 4px solid var(--accent);
  }
  .wordmark-name {
    color: var(--text-light);
    font-weight: 700;
    font-size: 28px;
    letter-spacing: 1px;
    text-transform: uppercase;
  }
  .card-front .wordmark { left: 42px; top: 44px; }
  .contact {
    position: absolute; left: 42px; bottom: 48px; z-index: 1;
    color: var(--text-light);
    font-style: italic; font-size: 16px; line-height: 1.55;
  }
  .contact-address { margin-bottom: 8px; }
  .contact-row { display: flex; align-items: center; gap: 10px; }
  .contact-row svg { width: 16px; height: 16px; flex: none; }
  .holder {
    position: absolute; right: 40px; top: 150px; text-align: right; z-index: 1;
  }
  .holder-name {
    color: var(--accent); font-weight: 700; font-size: 22px;
    text-transform: uppercase; letter-spacing: 0.5px;
  }
  .holder-role {
    color: var(--text-light); font-style: italic; font-size: 17px; margin-top: 4px;
  }
  .edge-tab {
    position: absolute; right: 0; top: 196px; z-index: 1;
    width: 14px; height: 44px;
    background: var(--accent);
    border-radius: 6px 0 0 6px;
  }
  .card-back .wordmark {
    left: 50%; top: 50%; transform: translate(-50%, -50%);
  }
  .card-back .wordmark-name { font-size: 32px; }
  .card-back .wordmark-square { width: 34px; height: 34px; }
</style>
</head>
<body>
<main class="sheet">
  <section class="card card-front">
    <span class="backdrop-frame"></span>
    <div class="wordmark">
      <span class="wordmark-square"></span>
      <span class="wordmark-name">Halvenmoor Consulting</span>
    </div>

    <div class="contact">
      <p class="contact-address">Your Address<br>City, State, Zip 0000</p>
      <p class="contact-row">
        <svg viewBox="0 0 16 16" aria-hidden="true"><path fill="var(--accent)" d="M3.5 1.5l2.5 0 1.2 3-1.6 1.2a8 8 0 0 0 4.7 4.7l1.2-1.6 3 1.2v2.5c0 .8-.7 1.5-1.5 1.5A12.5 12.5 0 0 1 2 3c0-.8.7-1.5 1.5-1.5z"/></svg>
        555-014-2100
      </p>
      <p class="contact-row">
        <svg viewBox="0 0 16 16" aria-hidden="true"><rect x="1" y="3" width="14" height="10" rx="1" fill="var(--accent)"/><path d="M1.5 3.5L8 9l6.5-5.5" stroke="var(--card-bg)" stroke-width="1.4" fill="none"/></svg>
        hello@halvenmoor.com
      </p>
      <p class="contact-row">
        <svg viewBox="0 0 16 16" aria-hidden="true"><circle cx="8" cy="8" r="7" fill="var(--accent)"/><path d="M1 8h14M8 1c-3 3.5-3 10.5 0 14M8 1c3 3.5 3 10.5 0 14" stroke="var(--card-bg)" stroke-width="1.1" fill="none"/></svg>
        www.halvenmoor.com
      </p>
    </div>

    <div class="holder">
      <p class="holder-name">Marcus Ellery</p>
      <p class="holder-role">Manager</p>
    </div>
    <span class="edge-tab"></span>
  </section>

  <section class="card card-back">
    <span class="backdrop-frame"></span>
    <div class="wordmark">
      <span class="wordmark-square"></span>
      <span class="wordmark-name">Halvenmoor Consulting</span>
    </div>
  </section>
</main>
</body>
</html>
```